Business card for Crestline Bathrooms

Please design a business card for our bathroom renovation business. You can use my existing logo, but if you have an idea to modernize it, I would like to see it. Please see attached files first. I would like to use the blue and the orange theme. I like the concept of using the shower head in the logo. Please find following a design (or two) that I have been trying to create with my limited resources. That design was for a sign, but I was going to adopt it and use it as a business card as well. I like the concept of the water splash but I don’t think it “flows” nicely together with the logo. Another thought is that maybe creating the logo out of water splash could work and have a dramatic effect (like the water text and the butterfly picture attached with similar background instead of white). If the above doesn’t work I would like to see a modern simplified design. One of the attached files named as the unwanted business card has all the details that I want included in the business card. Please note that it is two sided.
Updates

I am very thankful for the designs that I have received, but they are very similar and only a couple of attempts to do something with the water splash as per my original brief. Modernizing the logo and having it made out of out of water splash with the orange as color accent could work and have a dramatic effect (like the water text and the butterfly picture attached with similar background instead of white). Please do not use the butterfly itself! This is just an example that images can be created out of water splash.

Contact Information for Business Card

all the details are on the unwonted business card file included

Colors
3176b5

Requirements
Nice to have
• Copied from the brief:
• ... maybe creating the logo out of water splash could work and have a dramatic effect (like the water text and the butterfly picture attached with similar background instead of white). Please do not use the butterfly itself!
Should not have
• I am getting designs with a butterfly. The butterfly picture was an example of creating something from a water splash. The butterfly itself has no association with anything other than the concept of creating a logo out of water splash. Sorry, I thought I was clear in the brief.

```html
<!DOCTYPE html>
<html lang="en">
<head>
<meta charset="utf-8">
<title>Crestline Bathrooms – Business Card</title>
<link rel="stylesheet" href="https://fonts.googleapis.com/css2?family=Roboto:wght@400;500&family=Short+Stack&display=swap">
<style>
  :root {
    --navy: #1a4a72;
    --coral: #e8735f;
    --grey-text: #4a4a4a;
    --sky: #bfe0f8;
    --sky-soft: #dff0fc;
    --white: #ffffff;
    --backdrop: #e4e4e4;
    --badge: #5a5a5a;
  }
  * { box-sizing: border-box; margin: 0; padding: 0; }
  html, body {
    width: 1200px; height: 960px; overflow: hidden;
    background: var(--backdrop);
    font-family: "Roboto", Arial, sans-serif;
  }
  .card {
    position: absolute;
    width: 600px; height: 343px;
    overflow: hidden;
    box-shadow: 1px 2px 4px rgba(0,0,0,0.35);
  }
  .card-front {
    left: 300px; top: 113px;
    background: linear-gradient(120deg, var(--white) 0%, var(--white) 30%, var(--sky-soft) 60%, var(--sky) 100%);
  }
  .card-back {
    left: 300px; top: 472px;
    background: linear-gradient(60deg, var(--sky) 0%, var(--sky-soft) 40%, var(--white) 75%, var(--white) 100%);
  }
  .water-splash {
    position: absolute;
    border-radius: 50% 40% 45% 55%;
  }
  .card-front .water-splash {
    left: 300px; top: 0; width: 300px; height: 245px;
    background: radial-gradient(ellipse at 60% 45%, rgba(70,150,200,0.55) 0%, rgba(120,190,230,0.35) 45%, rgba(191,224,248,0) 72%);
  }
  .card-back .water-splash {
    left: 300px; top: 0; width: 300px; height: 250px;
    background: radial-gradient(ellipse at 65% 45%, rgba(150,200,225,0.35) 0%, rgba(190,225,240,0.2) 45%, rgba(255,255,255,0) 72%);
  }
  .brand {
    position: absolute;
    display: flex; align-items: center; gap: 10px;
  }
  .brand-dot {
    width: 22px; height: 22px; border-radius: 50%;
    background: var(--coral); flex: none;
  }
  .brand-name {
    font-family: "Roboto", Arial, sans-serif;
    font-weight: 500;
    color: var(--navy);
    line-height: 1.05;
  }
  .card-front .brand { left: 46px; top: 78px; }
  .card-front .brand-name { font-size: 30px; }
  .card-back .brand { left: 52px; top: 138px; }
  .card-back .brand-name { font-size: 32px; }
  .holder-name {
    position: absolute; left: 44px; top: 226px;
    font-family: "Short Stack", "Comic Sans MS", cursive;
    font-size: 23px; color: var(--navy);
  }
  .postal-address {
    position: absolute; left: 45px; top: 270px;
    font-size: 14.5px; line-height: 19px; color: var(--grey-text);
    font-style: normal;
  }
  .contact-list {
    position: absolute; left: 345px; top: 231px;
    list-style: none;
  }
  .contact-list li {
    display: flex; align-items: center; gap: 7px;
    font-size: 14.5px; line-height: 19px; color: var(--grey-text);
  }
  .contact-list svg { width: 13px; height: 13px; fill: var(--navy); flex: none; }
  .divider-rule {
    position: absolute; left: 304px; top: 48px;
    width: 2px; height: 252px; background: var(--coral);
  }
  .service-list {
    position: absolute; left: 338px; top: 45px;
    list-style: none;
  }
  .service-list li {
    position: relative; padding-left: 17px;
    font-size: 14.5px; line-height: 19px; color: var(--grey-text);
    margin-bottom: 19px;
  }
  .service-list li::before {
    content: ""; position: absolute; left: 0; top: 6px;
    width: 6px; height: 6px; border-radius: 50%; background: var(--navy);
  }
  .membership-badges {
    position: absolute; left: 340px; top: 265px;
    display: flex; align-items: center; gap: 17px;
  }
  .badge-square { width: 32px; height: 34px; background: var(--badge); border-radius: 4px; }
  .badge-sep { width: 1px; height: 34px; background: var(--badge); }
  .badge-bar { width: 118px; height: 28px; background: var(--badge); border-radius: 2px; }
</style>
</head>
<body>

<section class="card card-front" aria-label="Business card front">
  <div class="water-splash" role="img" aria-label="Flowing blue water splash"></div>
  <div class="brand">
    <span class="brand-dot"></span>
    <span class="brand-name">Crestline<br>Bathrooms</span>
  </div>
  <h1 class="holder-name">Daniel Moretti</h1>
  <address class="postal-address">PO Box 48<br>Hollydale 2700</address>
  <ul class="contact-list">
    <li><svg viewBox="0 0 24 24"><path d="M6.6 10.8a15 15 0 0 0 6.6 6.6l2.2-2.2c.3-.3.7-.4 1-.2 1.1.4 2.3.6 3.6.6.6 0 1 .4 1 1V20c0 .6-.4 1-1 1A17 17 0 0 1 3 4c0-.6.4-1 1-1h3.5c.6 0 1 .4 1 1 0 1.3.2 2.5.6 3.6.1.3 0 .7-.2 1z"/></svg>0400 555 218</li>
    <li><svg viewBox="0 0 24 24"><path d="M7 1h10a2 2 0 0 1 2 2v18a2 2 0 0 1-2 2H7a2 2 0 0 1-2-2V3a2 2 0 0 1 2-2zm0 3v14h10V4zm5 15.5a1.2 1.2 0 1 0 0 2.4 1.2 1.2 0 0 0 0-2.4z"/></svg>6200 4417</li>
    <li><svg viewBox="0 0 24 24"><path d="M2 5h20v14H2zm2 2v.5l8 5 8-5V7l-8 5z"/></svg>daniel@crestlinebathrooms.com.au</li>
    <li><svg viewBox="0 0 24 24"><path d="M12 2a10 10 0 1 0 0 20 10 10 0 0 0 0-20zm-1 17.9A8 8 0 0 1 4.2 10.5L9 15.3v1a2 2 0 0 0 2 2zm6.9-2.5a2 2 0 0 0-1.9-1.4h-1v-3a1 1 0 0 0-1-1H8v-2h2a1 1 0 0 0 1-1V7h2a2 2 0 0 0 2-2v-.4a8 8 0 0 1 2.9 12.8z"/></svg>crestlinebathrooms.com.au</li>
  </ul>
</section>

<section class="card card-back" aria-label="Business card back">
  <div class="water-splash" role="img" aria-label="Faint water splash"></div>
  <div class="brand">
    <span class="brand-dot"></span>
    <span class="brand-name">Crestline<br>Bathrooms</span>
  </div>
  <div class="divider-rule"></div>
  <ul class="service-list">
    <li>Complete Bathroom<br>Renovations &amp; Remodelling</li>
    <li>Highly Skilled &amp;<br>Qualified Tradespeople</li>
    <li>Professional Service From<br>Concept To Completion</li>
    <li>All Work Guaranteed</li>
  </ul>
  <div class="membership-badges">
    <span class="badge-square" role="img" aria-label="Industry association badge"></span>
    <span class="badge-sep"></span>
    <span class="badge-bar" role="img" aria-label="Builders association badge"></span>
  </div>
</section>

</body>
</html>
```